Emerging automotive detailing business

I am starting a small automotive detailing business in hopes of becoming a well-known detailer to work on high end cars. I would like a card to reflect the high quality and time I put into my work. The name of the company is Bright Crest Detailing. I feel like it represents racecars getting off the line at the drag strip as well as an innuendo of "Up the Ladder". I do minor paint correction such as clay barring, multi-step buffing and polishing, waxing, hand washes, etc. I am always striving to learn more and improve my work. My goal is to have total customer satisfaction. This is a female run business but I do not want it to be very girly. Elegant is okay! I have pictures of my personal wrenfield attached, they do not need to be incorporated but if you can think of a cool way to use 1 or all of them, go for it!

Target Market(s)

Anyone that owns a vehicle. Preferably high end vehicles such as Valtori, Castellverde and Morvani but I will also happily work on any car, truck or suv no matter what brand.

Industry/Entity Type

Automotive

Contact Information for Business Card

Bright Crest Detailing
Mira Tolland
4175 Quenhollow Rd
Ashmere PA 17492
Cell phone- call/text- 717-555-0148
email- brightcrestdetails@maildrop-example.com
Instagram: @brightcrestdetailing
Facebook: facebook.com/brightcrestdetailing

Requirements
Must have
• Business name, my name, address, phone number. Listing that I do minor paint correction such as clay barring, multi-step buffing and polishing, waxing, hand washes, interior cleaning, and more. (This last part was in nice to haves but I have realized that I do really want it, so I moved it to must haves.) I want something that is different and eye-catching to my customers. Some people have done this very well with cards already submitted to me, but a lot have not. I didn't mess with the "look and feel bars" much because because I am pretty open to the overall design as long as it is not your basic run of the mill design.
Nice to have
• Something car related. Maybe an appointment time/date line. I do not have a logo, but if you would like to design one and incorporate it, that would be amazing!
Should not have
• Purple and Pink colors. Boring, basic, normal card.

```html
<!DOCTYPE html>
<html lang="en">
<head>
<meta charset="utf-8">
<title>Bright Crest Detailing – Business Card</title>
<link rel="stylesheet" href="https://fonts.googleapis.com/css2?family=Tinos&family=Arimo:wght@400&family=Quicksand:wght@300&display=swap">
<style>
  :root {
    --backdrop: #e6e4e0;
    --card: #fbfbfa;
    --ink: #1c1c1c;
    --muted: #555555;
    --band: #151515;
    --rule: #222222;
  }
  * { margin: 0; padding: 0; box-sizing: border-box; }
  html, body { width: 1200px; height: 892px; overflow: hidden; }
  body {
    background: var(--backdrop);
    display: flex;
    flex-direction: column;
    align-items: center;
    justify-content: center;
    gap: 40px;
    color: var(--ink);
  }
  .card {
    position: relative;
    width: 640px;
    height: 366px;
    background: var(--card);
    box-shadow: 0 4px 14px rgba(0,0,0,0.18);
    overflow: hidden;
  }

  /* Front */
  .front-title {
    position: absolute;
    top: 74px; left: 0; right: 0;
    text-align: center;
    font-family: "Tinos", serif;
    font-weight: 400;
    font-size: 38px;
    letter-spacing: 0.5px;
  }
  .front-name {
    position: absolute;
    top: 128px; left: 0; right: 0;
    text-align: center;
    font-family: "Arimo", sans-serif;
    font-size: 24px;
  }
  .front-services {
    position: absolute;
    top: 192px; left: 30px; right: 30px;
    text-align: center;
    font-family: "Arimo", sans-serif;
    font-size: 13px;
    letter-spacing: 0.3px;
    color: var(--muted);
  }
  .front-rule {
    position: absolute;
    left: 0; top: 252px;
    width: 640px; height: 40px;
  }
  .front-address {
    position: absolute;
    left: 122px; top: 290px;
    font-family: "Arimo", sans-serif;
    font-size: 20px;
  }

  /* Back */
  .back-band { position: absolute; left: 0; top: 0; width: 640px; height: 366px; }
  .back-title {
    position: absolute;
    right: 48px; top: 58px;
    font-family: "Quicksand", sans-serif;
    font-weight: 300;
    font-size: 34px;
  }
  .back-name {
    position: absolute;
    right: 78px; top: 108px;
    font-family: "Arimo", sans-serif;
    font-weight: 400;
    font-size: 28px;
  }
  .contact-list {
    position: absolute;
    left: 150px; top: 196px;
    list-style: none;
    font-family: "Arimo", sans-serif;
    font-size: 18px;
  }
  .contact-item {
    display: flex;
    align-items: center;
    gap: 10px;
    height: 32px;
  }
  .contact-icon { width: 16px; height: 16px; flex: none; }
</style>
</head>
<body>

  <section class="card card-front">
    <h1 class="front-title">Bright Crest Detailing</h1>
    <p class="front-name">Mira Tolland</p>
    <p class="front-services">Clay Barring · Multi-Step Buffing &amp; Polishing · Waxing · Hand Washes · Interior Cleaning</p>
    <svg class="front-rule" viewBox="0 0 640 40" aria-hidden="true">
      <line x1="0" y1="22" x2="98" y2="22" stroke="var(--rule)" stroke-width="2"/>
      <line x1="126" y1="22" x2="640" y2="22" stroke="var(--rule)" stroke-width="2"/>
      <path d="M112 32 C104 22 100 17 100 11 A12 12 0 0 1 124 11 C124 17 120 22 112 32 Z" fill="var(--ink)"/>
      <circle cx="112" cy="11" r="4.5" fill="var(--card)"/>
    </svg>
    <p class="front-address">4175 Quenhollow Rd, Ashmere PA 17492</p>
  </section>

  <section class="card card-back">
    <svg class="back-band" viewBox="0 0 640 366" aria-hidden="true">
      <path d="M0 0 H120 Q40 150 30 366 H0 Z" fill="var(--band)"/>
    </svg>
    <h2 class="back-title">Bright Crest Detailing</h2>
    <p class="back-name">Mira Tolland</p>
    <ul class="contact-list">
      <li class="contact-item">
        <svg class="contact-icon" viewBox="0 0 16 16" aria-hidden="true">
          <rect width="16" height="16" fill="var(--ink)"/>
          <path d="M5 3 L7 3 L7.6 6 L6.3 6.8 Q7.5 9.2 9.2 9.8 L10 8.5 L13 9 L13 11 Q12.5 13 10.5 12.8 Q4 11.5 3.2 5 Q3 3.2 5 3 Z" fill="var(--card)"/>
        </svg>
        <span>717-555-0148</span>
      </li>
      <li class="contact-item">
        <svg class="contact-icon" viewBox="0 0 16 16" aria-hidden="true">
          <rect width="16" height="16" fill="var(--ink)"/>
        </svg>
        <span>@brightcrestdetailing</span>
      </li>
      <li class="contact-item">
        <svg class="contact-icon" viewBox="0 0 16 16" aria-hidden="true">
          <rect width="16" height="16" fill="var(--ink)"/>
          <rect x="3" y="5" width="10" height="7" fill="none" stroke="var(--card)" stroke-width="1.2"/>
          <path d="M3 5 L8 9 L13 5" fill="none" stroke="var(--card)" stroke-width="1.2"/>
        </svg>
        <span>brightcrestdetails@maildrop-example.com</span>
      </li>
      <li class="contact-item">
        <svg class="contact-icon" viewBox="0 0 16 16" aria-hidden="true">
          <rect width="16" height="16" fill="var(--ink)"/>
          <path d="M8 14 C5 10 4.5 8.5 4.5 6.5 A3.5 3.5 0 0 1 11.5 6.5 C11.5 8.5 11 10 8 14 Z" fill="var(--card)"/>
          <circle cx="8" cy="6.5" r="1.3" fill="var(--ink)"/>
        </svg>
        <span>4175 Quenhollow Rd, Ashmere PA 17492</span>
      </li>
    </ul>
  </section>

</body>
</html>
```